ultra-minimalist business card

front (black background, matte):

reza t. kovin
writer | photographer
get@rezakovin.com

back (white background, matte):

a picture speaks a thousand words;
a word draws a thousand pictures.

www.rezakovin.com

all text should be small (white or silver - as long as it shows against the black - on the front; black or gray - as long as it shows against the white - on the back).

feel free to get creative in terms of arrangement, alignment, and font type, but remember, the overall style is minimalist, so nothing too fancy, please.

thanks.

```html
<!DOCTYPE html>
<html lang="en">
<head>
<meta charset="utf-8">
<title>Reza T. Kovin — Business Card</title>
<link rel="stylesheet" href="https://fonts.googleapis.com/css2?family=Arimo:wght@400;700&display=swap">
<style>
  :root {
    --page-bg: #e9e8e6;
    --card-black: #141517;
    --emboss-black: #1c1e21;
    --silver: #d4d6d8;
    --card-white: #fbfbfb;
    --photo-light: #f1f1f1;
    --photo-mid: #dcdcdc;
    --ink: #1a1a1a;
    --card-shadow: rgba(0, 0, 0, 0.18);
  }
  * { margin: 0; padding: 0; box-sizing: border-box; }
  html, body {
    width: 1200px;
    height: 780px;
    overflow: hidden;
    background: var(--page-bg);
    font-family: "Arimo", Arial, sans-serif;
  }
  .canvas {
    position: relative;
    width: 1200px;
    height: 780px;
    display: flex;
    align-items: center;
    justify-content: center;
    gap: 50px;
  }
  .card {
    position: relative;
    width: 500px;
    height: 286px;
    border-radius: 3px;
    overflow: hidden;
    box-shadow: 0 10px 30px var(--card-shadow);
  }

  /* Front */
  .card--front { background: var(--card-black); }
  .emboss-name {
    position: absolute;
    left: 18px;
    top: 24px;
    writing-mode: vertical-rl;
    transform: rotate(180deg);
    font-size: 26px;
    font-weight: 700;
    letter-spacing: 0.5px;
    color: var(--emboss-black);
    text-shadow: 0 1px 0 rgba(255,255,255,0.03), 0 -1px 0 rgba(0,0,0,0.5);
  }
  .contact {
    position: absolute;
    left: 318px;
    bottom: 40px;
    color: var(--silver);
    font-size: 12.5px;
    line-height: 1.45;
  }
  .contact__name { font-size: 15px; margin-bottom: 1px; }
  .contact__email { margin-top: 10px; }

  /* Back */
  .card--back { background: var(--card-white); }
  .photo-field {
    position: absolute;
    inset: 0;
    background:
      radial-gradient(ellipse 70% 90% at 30% 60%, var(--photo-mid) 0%, transparent 70%),
      linear-gradient(135deg, var(--photo-light) 0%, var(--photo-mid) 55%, var(--photo-light) 100%);
    opacity: 0.75;
  }
  .quote-block {
    position: absolute;
    left: 205px;
    top: 92px;
    color: var(--ink);
    font-size: 14px;
    line-height: 1.3;
  }
  .quote-block__web { margin-top: 38px; }
</style>
</head>
<body>
  <main class="canvas">
    <section class="card card--front" aria-label="Card front">
      <div class="emboss-name">Reza Kovin</div>
      <div class="contact">
        <p class="contact__name">Reza T. Kovin</p>
        <p class="contact__role">writer | photographer</p>
        <p class="contact__email">E: get@rezakovin.com</p>
      </div>
    </section>

    <section class="card card--back" aria-label="Card back">
      <div class="photo-field" role="img" aria-label="Faint black and white photograph of curved architectural roof structure"></div>
      <div class="quote-block">
        <p>a picture speaks a thousand words.</p>
        <p>a word draws a thousand pictures.</p>
        <p class="quote-block__web">www.rezakovin.com</p>
      </div>
    </section>
  </main>
</body>
</html>
```